wealth management firm, professional group, new model

we have a logo that works but we need a card, white background using our colors...clean look

our tag line if can be used in

Your Path From Saver to Steward

```html
<!DOCTYPE html>
<html lang="en">
<head>
<meta charset="utf-8">
<title>Arvel Wealth Partners – Business Card</title>
<link href="https://fonts.googleapis.com/css2?family=Lato:wght@400;700;900&display=swap" rel="stylesheet">
<style>
  :root {
    --navy: #1b2d4f;
    --ink: #1b2d4f;
    --grey-text: #555a61;
    --paper: #ffffff;
    --backdrop: #e9e9e9;
  }
  * { box-sizing: border-box; margin: 0; padding: 0; }
  html, body { width: 1200px; height: 1000px; overflow: hidden; }
  body {
    background: var(--backdrop);
    position: relative;
    font-family: 'Lato', sans-serif;
  }
  .card {
    position: absolute;
    left: 254px;
    width: 693px;
    height: 395px;
    border-radius: 20px;
    overflow: hidden;
  }
  .card--front { top: 78px; background: var(--paper); }
  .card--back { top: 526px; background: var(--navy); }

  .front__band {
    position: absolute; left: 0; right: 0; bottom: 0;
    height: 14px; background: var(--navy);
  }
  .brand {
    position: absolute; left: 60px; width: 275px; top: 184px;
    text-align: center; color: var(--ink); font-weight: 400;
  }
  .brand__name {
    font-size: 38px; letter-spacing: 20px; padding-left: 20px; line-height: 1;
  }
  .brand__sub {
    margin-top: 22px; font-size: 14.5px; letter-spacing: 2.4px;
  }
  .divider {
    position: absolute; left: 347px; top: 85px;
    width: 2px; height: 225px; background: var(--navy);
  }
  .contact { position: absolute; left: 387px; top: 80px; }
  .contact__name {
    font-size: 30px; font-weight: 900; color: var(--ink);
    letter-spacing: 0.5px; line-height: 1.1;
  }
  .contact__role {
    font-size: 17px; font-weight: 400; color: var(--grey-text); margin-top: 1px;
  }
  .contact__list { list-style: none; margin-top: 10px; }
  .contact__item {
    display: flex; align-items: flex-start; gap: 10px;
    font-size: 16px; color: var(--grey-text); line-height: 21px;
    margin-bottom: 3px; letter-spacing: 0.3px;
  }
  .contact__item--address { margin-bottom: 8px; }
  .contact__item svg { flex: none; width: 14px; height: 14px; margin-top: 3px; fill: var(--navy); }

  .back__name {
    position: absolute; left: 0; right: 0; top: 168px;
    text-align: center; color: var(--paper);
    font-size: 46px; font-weight: 400; letter-spacing: 22px; padding-left: 22px;
  }
  .back__tagline {
    position: absolute; left: 0; right: 0; top: 332px;
    text-align: center; color: var(--paper);
    font-size: 16px; letter-spacing: 0.2px;
  }
</style>
</head>
<body>
  <section class="card card--front">
    <div class="brand">
      <div class="brand__name">ARVEL</div>
      <div class="brand__sub">WEALTH PARTNERS</div>
    </div>
    <div class="divider"></div>
    <div class="contact">
      <div class="contact__name">MARCUS HALE</div>
      <div class="contact__role">Founder &amp; CEO</div>
      <ul class="contact__list">
        <li class="contact__item contact__item--address">
          <svg viewBox="0 0 14 14"><path d="M7 0a5 5 0 0 0-5 5c0 3.5 5 9 5 9s5-5.5 5-9a5 5 0 0 0-5-5zm0 7a2 2 0 1 1 0-4 2 2 0 0 1 0 4z"/></svg>
          <span>Street Address Here, City<br>State, Country, ZIP 123</span>
        </li>
        <li class="contact__item">
          <svg viewBox="0 0 14 14"><path d="M3 1l2 0 1.2 3-1.5 1.2a8 8 0 0 0 4 4L10 7.8l3 1.2V11a2 2 0 0 1-2 2A10 10 0 0 1 1 3a2 2 0 0 1 2-2z"/></svg>
          <span>(123) 456-7890</span>
        </li>
        <li class="contact__item">
          <svg viewBox="0 0 14 14"><path d="M4 0h6a1 1 0 0 1 1 1v12a1 1 0 0 1-1 1H4a1 1 0 0 1-1-1V1a1 1 0 0 1 1-1zm0.5 2v8h5V2zM7 11a.8.8 0 1 0 0 1.6A.8.8 0 0 0 7 11z"/></svg>
          <span>(123) 456-7890</span>
        </li>
        <li class="contact__item">
          <svg viewBox="0 0 14 14"><path d="M3 0h8v4H3zM1 5h12a1 1 0 0 1 1 1v5h-3v3H3v-3H0V6a1 1 0 0 1 1-1zm3 5v3h6v-3z"/></svg>
          <span>(123) 456-7890</span>
        </li>
        <li class="contact__item">
          <svg viewBox="0 0 14 14"><path d="M0 3h14v1L7 8 0 4zM0 5.3l7 4 7-4V11H0z"/></svg>
          <span>info@yourwebsitehere.com</span>
        </li>
        <li class="contact__item">
          <svg viewBox="0 0 14 14"><path d="M7 0a7 7 0 1 0 0 14A7 7 0 0 0 7 0zm4.8 5H9.6a10 10 0 0 0-1-3.3A5.5 5.5 0 0 1 11.8 5zM7 1.6c.6.8 1 2 1.2 3.4H5.8C6 3.6 6.4 2.4 7 1.6zM1.6 8.5a5.6 5.6 0 0 1 0-3h2.7a11 11 0 0 0 0 3zm.6 1h2.2a10 10 0 0 0 1 3.3 5.5 5.5 0 0 1-3.2-3.3zM7 12.4c-.6-.8-1-2-1.2-3.4h2.4C8 10.4 7.6 11.6 7 12.4zm1.6-.6a10 10 0 0 0 1-3.3h2.2a5.5 5.5 0 0 1-3.2 3.3zM9.7 8.5a11 11 0 0 0 0-3h2.7a5.6 5.6 0 0 1 0 3z"/></svg>
          <span>yourwebsitehere.com</span>
        </li>
      </ul>
    </div>
    <div class="front__band"></div>
  </section>

  <section class="card card--back">
    <div class="back__name">ARVEL</div>
    <p class="back__tagline">Your Path From Saver to Steward</p>
  </section>
</body>
</html>
```